KLR Buildworks - Civil Construction Construction Company (Telecommunications)

Need a basic website to refine our branding to a current reflection of our service offerings. KLR Buildworks provides civil construction services specializing in telecommunication sector.
I have started to create a website using word press. I would like to have someone refine the design and polish the overall look and functionality of the site. I would like to website to function in the wordpress format to allow for future edits and control of site.
Included site preview:
https://pvhosts-ua.pagemakerbench.example/7e2d94fa.com/Admin/index.html/qm_draft_view

```html
<!DOCTYPE html>
<html lang="en">
<head>
<meta charset="utf-8">
<title>KLR Buildworks – Civil Construction</title>
<link href="https://fonts.googleapis.com/css2?family=Roboto+Condensed:wght@400;700&family=Poppins:wght@300;400;500&family=Roboto+Slab:wght@400;700&display=swap" rel="stylesheet">
<style>
:root{
  --red:#f03a3a;
  --red-deep:#d8282c;
  --black:#000;
  --ink:#111;
  --text:#555;
  --grey:#f2f2f2;
  --footer:#1c1c1c;
  --white:#fff;
  --cond:'Roboto Condensed',sans-serif;
  --sans:'Poppins',sans-serif;
  --slab:'Roboto Slab',serif;
}
*{box-sizing:border-box;margin:0;padding:0}
html,body{width:1200px;height:3300px;overflow:hidden}
body{position:relative;background:var(--white);font-family:var(--sans);color:var(--ink)}
.abs{position:absolute}
.photo{position:absolute}
.btn{position:absolute;display:flex;align-items:center;justify-content:center;font-family:var(--cond);font-weight:700;font-size:14px;text-transform:uppercase}
.btn-red{background:var(--red);color:var(--white)}
.btn-white{background:var(--white);color:var(--ink)}

/* header */
.brand{position:absolute;left:60px;top:14px;display:flex;align-items:center;gap:10px;font-family:var(--sans);font-size:29px;font-weight:400;letter-spacing:.5px;color:var(--ink)}
.brand .mark{width:22px;height:22px;background:var(--red)}
.contact-top{position:absolute;top:12px;display:flex;gap:14px;font-size:12.5px;line-height:19px;color:var(--ink)}
.contact-top strong{font-weight:500}

/* nav */
.nav{position:absolute;left:0;top:67px;width:1200px;height:42px;background:var(--black)}
.nav ul{list-style:none;display:flex;gap:32px;position:absolute;left:60px;top:14px;font-size:11.5px;font-weight:500;color:var(--white)}
.nav li.active{color:var(--red)}
.search{position:absolute;left:502px;top:9px;width:240px;height:23px;background:#333;color:#bbb;font-size:11.5px;padding:4px 10px}
.quote{position:absolute;left:930px;top:0;width:270px;height:42px;background:var(--red);clip-path:polygon(16px 0,100% 0,100% 100%,0 100%);color:var(--white);font-family:var(--cond);font-weight:700;font-size:15px;display:flex;align-items:center;justify-content:center}

/* hero */
.hero-title{position:absolute;left:60px;top:248px;font-family:var(--sans);font-weight:600;color:var(--white);line-height:1}
.hero-title .l1{font-size:82px;display:block}
.hero-title .l2{font-size:56px;display:block;margin-top:12px}
.hero-text{position:absolute;left:62px;top:412px;width:400px;font-family:var(--slab);font-size:12.5px;line-height:20px;color:var(--white)}
.service{position:absolute;top:652px;width:180px;height:165px}
.service .tag{position:absolute;right:0;bottom:0;width:56px;height:48px;background:var(--red);clip-path:polygon(22% 0,100% 0,100% 100%,0 100%)}
.service .tag svg{position:absolute;right:12px;top:10px}
.service-label{position:absolute;left:25px;top:48px;font-family:var(--slab);font-weight:700;font-size:15px;line-height:24px;color:var(--white)}

/* profile */
h2{font-family:var(--cond);font-weight:700;color:var(--ink)}
.profile h2{position:absolute;left:637px;top:932px;font-size:40px}
.para{position:absolute;font-size:12.5px;line-height:19.5px;color:var(--text)}
.para-quote{font-family:var(--slab);font-weight:700;color:var(--ink);font-size:12px}
.red-label{position:absolute;left:213px;top:1005px;width:113px;height:92px;background:var(--red);color:var(--white);font-family:var(--sans);font-weight:500;font-size:15px;line-height:23px;padding:16px 0 0 9px}

/* services dark */
.dark{position:absolute;left:0;top:1345px;width:600px;height:375px;background:var(--black)}
.dark h2{position:absolute;left:61px;top:56px;font-size:38px;line-height:45px;color:var(--white)}
.dark p{position:absolute;left:61px;top:158px;width:440px;font-size:12.5px;line-height:19.5px;color:var(--white)}

/* projects */
.projects h2{position:absolute;left:61px;top:1792px;font-size:40px}
.arrow{position:absolute;top:1796px;width:38px;height:38px;border-radius:50%;display:flex;align-items:center;justify-content:center}
.proj-label{position:absolute;left:315px;top:2105px;width:172px;height:60px;background:var(--white);clip-path:polygon(0 0,83% 0,100% 100%,0 100%);font-family:var(--slab);font-weight:700;font-size:15px;padding:20px 0 0 23px}

/* quote band */
.band{position:absolute;left:0;top:2208px;width:1200px;height:336px;background:linear-gradient(100deg,var(--red) 0%,#f24545 50%,#e03434 100%)}
.band q{position:absolute;left:61px;top:66px;width:760px;font-family:var(--sans);font-weight:500;font-size:38px;line-height:46px;color:var(--white);quotes:'"' '"'}

/* contact */
.contact h2{position:absolute;left:61px;top:2618px;font-size:40px}
.field{position:absolute;background:#f7f7f7;border:1px solid #e2e2e2;font-size:12px;color:#555;padding:11px 11px}

/* footer */
.footer{position:absolute;left:0;top:2976px;width:1200px;height:290px;background:var(--footer);color:#ddd}
.footer h3{position:absolute;top:60px;font-family:var(--slab);font-weight:700;font-size:18px;color:var(--red)}
.footer ul{position:absolute;list-style:none;font-size:12px;line-height:27px;color:#eee}
.footer .brand{color:var(--white);top:52px;font-size:25px}
.copy{position:absolute;left:0;top:3266px;width:1200px;height:34px;background:var(--red);color:var(--white);font-size:12px;display:flex;align-items:center;justify-content:center}
</style>
</head>
<body>

<header>
  <div class="brand"><span class="mark"></span>KLR BUILDWORKS</div>
  <div class="contact-top" style="left:740px">
    <svg width="28" height="28" viewBox="0 0 24 24" fill="none" stroke="#f03a3a" stroke-width="1.6"><path d="M5 3h4l2 5-2.5 1.5a11 11 0 0 0 6 6L16 13l5 2v4a2 2 0 0 1-2 2A17 17 0 0 1 3 5a2 2 0 0 1 2-2z"/></svg>
    <div>CALL :<br><strong>1 (780) 555-0147</strong></div>
  </div>
  <div class="contact-top" style="left:942px">
    <svg width="24" height="28" viewBox="0 0 24 28" fill="none" stroke="#f03a3a" stroke-width="1.8"><path d="M12 26s9-9 9-15a9 9 0 0 0-18 0c0 6 9 15 9 15z"/><circle cx="12" cy="11" r="3.2"/></svg>
    <div>18 Cedarline Ave Spruce<br>Grove, AB T7X 0K4 Canada</div>
  </div>
</header>

<nav class="nav">
  <ul>
    <li class="active">HOME</li><li>COMPANY PROFILE</li><li>WHY CHOOSE US</li><li>OUR WORKS</li>
  </ul>
  <div class="search">Search Here....</div>
  <div class="quote">GET A QUOTE</div>
</nav>

<section class="hero">
  <div class="photo" role="img" aria-label="Crew member in hi-vis vest operating equipment on a grassy site with trucks behind" style="left:0;top:109px;width:1200px;height:596px;background:linear-gradient(160deg,#8aa0b3 0%,#6f8b67 45%,#3f5a33 75%,#2c3a25 100%)"></div>
  <div class="abs" style="left:0;top:109px;width:560px;height:596px;background:linear-gradient(180deg,rgba(232,52,52,.96),rgba(205,38,40,.93));clip-path:polygon(0 0,100% 0,77% 100%,0 100%)"></div>
  <h1 class="hero-title"><span class="l1">KLR</span><span class="l2">BUILDWORKS</span></h1>
  <p class="hero-text">We understand the unique challenges of deploying crews and completing civil construction projects within Western Canada's diverse geography, terrain and climate</p>
  <div class="btn btn-white" style="left:60px;top:500px;width:120px;height:37px">Contact Us</div>

  <div class="service" style="left:206px">
    <div class="photo" role="img" aria-label="Close-up of blue hydraulic machinery" style="inset:0;background:linear-gradient(135deg,#8a9aa6,#4f6d84 50%,#3b4a55)"></div>
    <div class="tag"><svg width="30" height="28" viewBox="0 0 30 28" fill="none" stroke="#fff" stroke-width="1.6"><circle cx="7" cy="7" r="4"/><rect x="16" y="4" width="9" height="7"/><rect x="3" y="16" width="9" height="7"/><rect x="16" y="16" width="9" height="7"/></svg></div>
  </div>
  <div class="service" style="left:408px">
    <div class="photo" role="img" aria-label="Tracked machine in an autumn forest" style="inset:0;background:linear-gradient(160deg,#1f2a3a,#6b5a2a 55%,#3a3420)"></div>
    <div class="service-label">Quality<br>Assurance<br>Management</div>
  </div>
  <div class="service" style="left:611px">
    <div class="photo" role="img" aria-label="Work site along a grassy road with trees" style="inset:0;background:linear-gradient(180deg,#c9d3dc 0%,#8ea07a 45%,#5f7d3f 100%)"></div>
    <div class="tag"><svg width="30" height="28" viewBox="0 0 30 28" fill="none" stroke="#fff" stroke-width="1.6"><circle cx="15" cy="9" r="5"/><path d="M15 14v6M7 24h16"/><circle cx="8" cy="26" r="1"/><circle cx="15" cy="26" r="1"/><circle cx="22" cy="26" r="1"/></svg></div>
  </div>
  <div class="service" style="left:813px">
    <div class="photo" role="img" aria-label="Boom truck working beside a commercial building" style="inset:0;background:linear-gradient(180deg,#c4ccd2 0%,#9aa3a5 50%,#6e7f58 100%)"></div>
    <div class="tag"><svg width="30" height="28" viewBox="0 0 30 28" fill="none" stroke="#fff" stroke-width="1.6"><path d="M15 3v10M10 8h10"/><path d="M3 16c3 0 6 4 9 8h6c3-4 6-8 9-8"/></svg></div>
  </div>
</section>

<section class="profile">
  <div class="abs" style="left:0;top:884px;width:360px;height:390px;background:var(--grey)"></div>
  <div class="abs" style="left:510px;top:967px;width:26px;height:262px;background:var(--red);clip-path:polygon(40% 0,100% 0,60% 100%,0 100%)"></div>
  <div class="photo" role="img" aria-label="Red tracked trencher carrying a cable reel under a blue sky" style="left:266px;top:937px;width:248px;height:292px;background:linear-gradient(180deg,#7fa8d4 0%,#b4c9d8 40%,#b33232 65%,#3a3a3a 100%)"></div>
  <div class="red-label">KLR<br>Buildworks</div>
  <svg class="abs" style="left:213px;top:1097px" width="53" height="36"><polygon points="0,0 53,0 53,36" fill="#c01f22"/></svg>

  <h2>Company Profile</h2>
  <p class="para" style="left:635px;top:990px;width:430px">KLR Buildworks is a safety conscious, productive and efficient construction firm capable of all facets of civil construction. We have completed thousands of projects across Alberta, Saskatchewan and British Columbia working within various industry sectors.</p>
  <p class="para para-quote" style="left:635px;top:1073px;width:410px">"At KLR Buildworks we strive to provide creative solutions, on-time, on-budget and beyond expectations"</p>
  <p class="para" style="left:635px;top:1118px;width:410px">Each of KLR's construction crews are dispatched with a full complement of late model equipment and tools required to complete civil underground construction projects in</p>
  <div class="btn btn-red" style="left:634px;top:1192px;width:120px;height:37px">Learn More</div>
</section>

<section class="services">
  <div class="dark">
    <h2>Civil construction services<br>Specializing</h2>
    <p>Each of KLR's construction crews are dispatched with a full complement of late model equipment and tools required to complete civil underground construction projects in a safe and efficient manner meeting all criteria established by client, governing bodies and site environments.</p>
    <div class="btn btn-red" style="left:60px;top:278px;width:120px;height:37px">Viwe More</div>
  </div>
  <div class="photo" role="img" aria-label="Operator on a yellow trencher pulling orange cable conduit on grass" style="left:600px;top:1345px;width:600px;height:375px;background:linear-gradient(160deg,#2d4a2a 0%,#b59a2c 45%,#d1ae2a 60%,#5a8a3a 100%)"></div>
</section>

<section class="projects">
  <h2>Our Project</h2>
  <div class="arrow" style="left:1001px;background:#fde3e3">
    <svg width="20" height="14" viewBox="0 0 20 14" fill="none" stroke="#111" stroke-width="1.8"><path d="M1 7h17M12 1l6 6-6 6"/></svg>
  </div>
  <div class="arrow" style="left:1053px;background:#ececec">
    <svg width="20" height="14" viewBox="0 0 20 14" fill="none" stroke="#111" stroke-width="1.8"><path d="M19 7H2M8 1 2 7l6 6"/></svg>
  </div>
  <div class="photo" role="img" aria-label="Yellow compact track loader on a grassy hillside" style="left:0;top:1870px;width:294px;height:314px;background:linear-gradient(170deg,#8a7a5a,#c9a430 50%,#6a7a3a)"></div>
  <div class="photo" role="img" aria-label="Machine with orange cable reel in a field" style="left:302px;top:1870px;width:294px;height:314px;background:linear-gradient(170deg,#c5ccd2,#b0603a 45%,#6b8a45)"></div>
  <div class="photo" role="img" aria-label="Yellow tractor against a blue sky" style="left:603px;top:1870px;width:295px;height:314px;background:linear-gradient(170deg,#3f7fd0,#e3c62a 50%,#5c9a3a)"></div>
  <div class="photo" role="img" aria-label="Tracked dozer in front of mountains" style="left:905px;top:1870px;width:295px;height:314px;background:linear-gradient(170deg,#9aa9b5,#b89a4a 50%,#4e4532)"></div>
  <div class="proj-label">Project Design</div>
</section>

<section class="band">
  <q>At KLR Buildworks we strive to provide creative solutions, on-time, on-budget and beyond expectations</q>
</section>

<section class="contact">
  <div class="abs" style="left:1086px;top:2467px;width:38px;height:433px;background:var(--black);clip-path:polygon(50% 0,100% 0,50% 100%,0 100%)"></div>
  <div class="photo" role="img" aria-label="Orange compact track loader on grass" style="left:727px;top:2467px;width:375px;height:433px;background:linear-gradient(170deg,#e8e8e8 0%,#d9462a 40%,#2a2a2a 70%,#5e8a3a 100%)"></div>
  <h2>Contact Us</h2>
  <div class="field" style="left:60px;top:2683px;width:180px;height:37px">Name :</div>
  <div class="field" style="left:255px;top:2683px;width:180px;height:37px">Email :</div>
  <div class="field" style="left:60px;top:2729px;width:375px;height:37px">Phone :</div>
  <div class="field" style="left:60px;top:2773px;width:375px;height:76px">Message :</div>
  <div class="btn btn-red" style="left:60px;top:2862px;width:120px;height:37px">Submit From</div>
</section>

<footer class="footer">
  <div class="brand"><span class="mark"></span>KLR BUILDWORKS</div>
  <h3 style="left:337px">Site Map</h3>
  <ul style="left:337px;top:87px"><li>- Home</li><li>- About Us</li><li>- Why CHoose Us</li><li>- Our Work</li><li>- Contact Us</li></ul>
  <h3 style="left:612px">Contact Us</h3>
  <svg class="abs" style="left:612px;top:96px" width="16" height="20" viewBox="0 0 24 28"><path d="M12 26s9-9 9-15a9 9 0 0 0-18 0c0 6 9 15 9 15z" fill="#f03a3a"/><circle cx="12" cy="11" r="3.2" fill="#1c1c1c"/></svg>
  <p class="abs" style="left:642px;top:94px;font-size:12px;line-height:20px;color:#eee">18 Cedarline Ave Spruce<br>Grove, AB T7X 0K4 Canada</p>
  <svg class="abs" style="left:610px;top:149px" width="18" height="18" viewBox="0 0 24 24"><path d="M5 3h4l2 5-2.5 1.5a11 11 0 0 0 6 6L16 13l5 2v4a2 2 0 0 1-2 2A17 17 0 0 1 3 5a2 2 0 0 1 2-2z" fill="#f03a3a"/></svg>
  <p class="abs" style="left:642px;top:150px;font-size:12px;color:#eee">1 (780) 555-0147</p>
  <h3 style="left:888px">Newsletter Signup</h3>
  <p class="abs" style="left:888px;top:90px;width:200px;font-size:12px;line-height:19px;color:#ccc">Stay always in touch subsribe to our newsletter.</p>
  <div class="abs" style="left:887px;top:130px;width:253px;height:37px;background:var(--white);font-size:12px;color:#333;padding:11px 9px">Enter Email Address..</div>
  <div class="btn btn-red" style="left:887px;top:183px;width:120px;height:37px">Subsribe</div>
</footer>
<div class="copy">2022 © KLR Buildworks- All Right Reserved .</div>

</body>
</html>
```